Business card for medical clinic

I need an upmarket, modern medical/health business card for my clinic

Contact Information for Business Card

name, address, email, qr code

```html
<!DOCTYPE html>
<html lang="en">
<head>
<meta charset="utf-8">
<title>Lumen Care Clinic – Business Card</title>
<link rel="stylesheet" href="https://fonts.googleapis.com/css2?family=Montserrat:wght@400;500;700&display=swap">
<style>
  :root {
    --stage: #e9ebee;
    --teal-dark: #0a4a6a;
    --teal-light: #0a8dbd;
    --brand-navy: #1d3a64;
    --accent-blue: #29a9e1;
    --band-navy: #1a2540;
    --ink: #1f2430;
    --paper: #ffffff;
  }
  * { box-sizing: border-box; margin: 0; padding: 0; }
  html, body { width: 1200px; height: 931px; overflow: hidden; }
  body { background: var(--stage); font-family: "Montserrat", sans-serif; position: relative; }

  .card {
    position: absolute;
    width: 580px;
    height: 330px;
    border-radius: 18px;
    overflow: hidden;
    box-shadow: 0 10px 24px rgba(0,0,0,0.18);
  }

  /* Back side */
  .card-back {
    left: 50px; top: 60px;
    background: linear-gradient(180deg, var(--teal-dark) 0%, var(--teal-light) 100%);
    display: flex; align-items: center; justify-content: center;
  }
  .brand {
    font-family: "Montserrat", sans-serif;
    font-weight: 700;
    white-space: nowrap;
    line-height: 1;
  }
  .card-back .brand { color: var(--paper); font-size: 34px; }

  /* Front side */
  .card-front { left: 570px; top: 540px; background: var(--paper); }
  .card-front .brand { position: absolute; left: 36px; top: 38px; color: var(--brand-navy); font-size: 22px; }

  .person { position: absolute; left: 36px; top: 118px; }
  .person-name { font-weight: 700; font-size: 26px; color: var(--brand-navy); line-height: 1; }
  .person-role { font-weight: 500; font-size: 13px; color: var(--ink); margin-top: 6px; }

  .divider {
    position: absolute; left: 36px; top: 172px; width: 508px; height: 1.5px;
    background: var(--accent-blue);
  }

  .contacts { position: absolute; left: 36px; top: 188px; list-style: none; }
  .contacts li { display: flex; align-items: center; gap: 10px; font-size: 13px; color: var(--ink); height: 24px; }
  .contacts svg { width: 14px; height: 14px; fill: var(--accent-blue); flex: none; }

  .footer-band {
    position: absolute; left: 0; bottom: 0; width: 100%; height: 12px;
    background: var(--accent-blue);
  }
  .address-block {
    position: absolute; right: 0; bottom: 0; width: 300px; height: 40px;
    background: var(--band-navy);
    clip-path: polygon(12px 0, 100% 0, 100% 100%, 0 100%);
    color: var(--paper); font-size: 11.5px; font-weight: 500;
    display: flex; align-items: center; justify-content: center;
    padding-left: 12px;
  }
</style>
</head>
<body>

  <section class="card card-back" aria-label="Card back">
    <div class="brand">Lumen Care Clinic</div>
  </section>

  <section class="card card-front" aria-label="Card front">
    <div class="brand">Lumen Care Clinic</div>

    <div class="person">
      <p class="person-name">Daniel Reyes</p>
      <p class="person-role">Managing Director</p>
    </div>
    <div class="divider"></div>

    <ul class="contacts">
      <li>
        <svg viewBox="0 0 24 24" aria-hidden="true"><path d="M6.6 10.8a15.1 15.1 0 0 0 6.6 6.6l2.2-2.2a1 1 0 0 1 1-.25 11.4 11.4 0 0 0 3.6.6 1 1 0 0 1 1 1V20a1 1 0 0 1-1 1A17 17 0 0 1 3 4a1 1 0 0 1 1-1h3.5a1 1 0 0 1 1 1c0 1.25.2 2.45.6 3.6a1 1 0 0 1-.25 1z"/></svg>
        555.014.2730
      </li>
      <li>
        <svg viewBox="0 0 24 24" aria-hidden="true"><path d="M2 5h20v14H2z M2 5l10 8 10-8"/></svg>
        info@lumencareclinic.com
      </li>
      <li>
        <svg viewBox="0 0 24 24" aria-hidden="true"><circle cx="12" cy="12" r="10"/></svg>
        www.lumencareclinic.com
      </li>
    </ul>

    <div class="footer-band"></div>
    <div class="address-block">48 Birch Hollow Lane Ridgeview, OR 97012</div>
  </section>

</body>
</html>
```